Velk Partners Building Business Cards

We need a business card that reflects our business as "Solar Experts" in San Diego. Browse our website www.velkpartners.example our License needs to be displayed as "CSLB# 3867140" our phone number is (619) 555-0187

Save thousands on your electric bills and increase the value of your home while helping to protect the environment. Our solar installation experts will help you design the system that's right for you, using only the highest quality equipment that will look great and give you ideal performance. Our goal is to make you energy independent, and get your electric bill to 0.

Paul Osterby
(619) 555-0187
paul@velkpartners.example

Target Market(s)

Home owners in san diego looking for solar

Industry/Entity Type

Solar Energy

Contact Information for Business Card

Paul Osterby
(619) 555-0187
paul@velkpartners.example

Font styles to use
Other font styles liked:
• Use our logo font

Requirements
Must have
• License needs to be displayed as "CSLB# 3867140" our phone number is (619) 555-0187
Nice to have
• Real images of rooftop home solar in san diego
Should not have
• our business address

```html
<!DOCTYPE html>
<html lang="en">
<head>
<meta charset="utf-8">
<title>Velk Partners Building – Business Cards</title>
<link rel="stylesheet" href="https://fonts.googleapis.com/css2?family=Poppins:wght@700&family=Noto+Serif:wght@400;700&display=swap">
<style>
  :root {
    --navy: #1b3a7a;
    --yellow: #f5ab1e;
    --paper: #ffffff;
    --backdrop: #b9b9b9;
    --solar-light: #6f8fc9;
    --solar-dark: #1f3f86;
    --ink-soft: #e9ecf4;
  }
  * { box-sizing: border-box; margin: 0; padding: 0; }
  html, body { width: 1200px; height: 837px; overflow: hidden; }
  body {
    background: var(--backdrop);
    display: flex;
    align-items: center;
    justify-content: center;
    gap: 40px;
  }
  .card {
    position: relative;
    width: 560px;
    height: 320px;
    background: var(--paper);
    overflow: hidden;
    box-shadow: 0 6px 18px rgba(0,0,0,0.18);
  }

  /* Back side: name and social row */
  .card-back .brand {
    position: absolute;
    left: 70px;
    top: 92px;
    width: 420px;
    font-family: "Poppins", sans-serif;
    font-weight: 700;
    font-size: 40px;
    line-height: 1.05;
    color: var(--navy);
    letter-spacing: -0.5px;
  }
  .social-row {
    position: absolute;
    left: 92px;
    top: 214px;
    display: flex;
    gap: 12px;
  }
  .social-row span {
    width: 24px;
    height: 24px;
    border-radius: 3px;
    background: var(--navy);
  }
  .social-row span:nth-child(even) { background: var(--yellow); }

  /* Front side */
  .solar-collage {
    position: absolute;
    left: 0;
    top: 0;
    width: 270px;
    height: 320px;
  }
  .card-front .brand {
    position: absolute;
    left: 290px;
    top: 34px;
    width: 250px;
    font-family: "Poppins", sans-serif;
    font-weight: 700;
    font-size: 30px;
    line-height: 1.05;
    color: var(--navy);
    letter-spacing: -0.4px;
  }
  .name-band {
    position: absolute;
    left: 300px;
    top: 148px;
    width: 230px;
    height: 38px;
    background: var(--yellow);
    display: flex;
    align-items: center;
    padding-left: 26px;
    font-family: "Noto Serif", serif;
    font-weight: 700;
    font-size: 18px;
    color: var(--navy);
  }
  .contact-list {
    position: absolute;
    left: 290px;
    top: 200px;
    list-style: none;
    font-family: "Noto Serif", serif;
    font-size: 14px;
    color: var(--navy);
  }
  .contact-list li {
    display: flex;
    align-items: center;
    gap: 10px;
    height: 24px;
  }
  .contact-icon {
    width: 20px;
    height: 20px;
    background: var(--yellow);
    border-radius: 2px;
    display: flex;
    align-items: center;
    justify-content: center;
    flex: none;
  }
  .license {
    position: absolute;
    left: 290px;
    top: 280px;
    font-family: "Noto Serif", serif;
    font-size: 14px;
    color: var(--navy);
  }
</style>
</head>
<body>

  <section class="card card-back" aria-label="Card back">
    <div class="brand">Velk Partners Building</div>
    <div class="social-row" aria-label="Social media links">
      <span></span><span></span><span></span><span></span>
    </div>
  </section>

  <section class="card card-front" aria-label="Card front">
    <svg class="solar-collage" viewBox="0 0 270 320" role="img" aria-label="Collage of rooftop solar panel photographs in hexagon frames">
      <defs>
        <linearGradient id="solarTone" x1="0" y1="0" x2="1" y2="1">
          <stop offset="0" stop-color="var(--solar-light)"/>
          <stop offset="1" stop-color="var(--solar-dark)"/>
        </linearGradient>
      </defs>
      <g fill="url(#solarTone)" stroke="var(--navy)" stroke-width="2.5">
        <polygon points="250,60 215,0.4 145,0.4 110,60 145,119.6 215,119.6"/>
        <polygon points="250,181 215,121.4 145,121.4 110,181 145,240.6 215,240.6"/>
        <polygon points="250,302 215,242.4 145,242.4 110,302 145,361.6 215,361.6"/>
        <polygon points="145,120 110,60.4 40,60.4 5,120 40,179.6 110,179.6"/>
        <polygon points="145,241 110,181.4 40,181.4 5,241 40,300.6 110,300.6"/>
        <polygon points="145,-1 110,-60.6 40,-60.6 5,-1 40,58.6 110,58.6"/>
        <polygon points="40,60 5,0.4 -65,0.4 -100,60 -65,119.6 5,119.6"/>
        <polygon points="40,181 5,121.4 -65,121.4 -100,181 -65,240.6 5,240.6"/>
        <polygon points="40,302 5,242.4 -65,242.4 -100,302 -65,361.6 5,361.6"/>
      </g>
    </svg>

    <div class="brand">Velk Partners Building</div>

    <div class="name-band">Paul Osterby</div>

    <ul class="contact-list">
      <li>
        <span class="contact-icon">
          <svg width="12" height="12" viewBox="0 0 24 24" aria-hidden="true"><path fill="#fff" d="M6.6 10.8c1.4 2.8 3.8 5.1 6.6 6.6l2.2-2.2c.3-.3.7-.4 1-.2 1.1.4 2.3.6 3.6.6.6 0 1 .4 1 1V20c0 .6-.4 1-1 1C10.6 21 3 13.4 3 4c0-.6.4-1 1-1h3.5c.6 0 1 .4 1 1 0 1.3.2 2.5.6 3.6.1.3 0 .7-.2 1z"/></svg>
        </span>
        (619) 555-0187
      </li>
      <li>
        <span class="contact-icon">
          <svg width="12" height="12" viewBox="0 0 24 24" aria-hidden="true"><path fill="#fff" d="M2 5h20v14H2z"/><path fill="none" stroke="var(--yellow)" stroke-width="2" d="M2 5l10 8 10-8"/></svg>
        </span>
        paul@velkpartners.example
      </li>
      <li>
        <span class="contact-icon">
          <svg width="12" height="12" viewBox="0 0 24 24" aria-hidden="true"><circle cx="12" cy="12" r="9" fill="none" stroke="#fff" stroke-width="2"/><path fill="none" stroke="#fff" stroke-width="1.6" d="M3 12h18M12 3c3 3 3 15 0 18M12 3c-3 3-3 15 0 18"/></svg>
        </span>
        www.velkpartners.example
      </li>
    </ul>

    <div class="license">CSLB# 3867140</div>
  </section>

</body>
</html>
```